Ravnaas-Lilleby Group AS

We need a design for our company including background pictures on our web (wix-template), redesign of logo and reports. Our company delivers personality test and services to clients when hiring staff or related to organizatonal developement.

Target Market(s)

Unisex, Age 30-50, managers in private corporations

Industry/Entity Type

Recruitment

Logo Text

Bygger laget sterkt (english translate: buids your team strong)

Number of Pages Required

1 page

Font styles to use
Sans Serif

Colors
add136
34a6d7
0255a3

Requirements
Must have
• The ideal designer will be the one to bring my narrative come to life. And it will have to include the testresults report and redesign (!) of my logo. Following the attached brief in ppt:
• - the testresult report
• - redesign logo
• - graphic elements in a maritime narrative
• - including the boat, the radar, 7 GULLs, the compass etc
Nice to have
• A strong narrative with a lot of elements.
• I really like the green color in the attached breif ;-)

```html
<!DOCTYPE html>
<html lang="en">
<head>
<meta charset="utf-8">
<title>Ravnaas-Lilleby Group – Test Result Report</title>
<link href="https://fonts.googleapis.com/css2?family=Lato:wght@400;700&display=swap" rel="stylesheet">
<style>
:root{
  --ink:#000;
  --white:#fff;
  --navy:#0d2f5a;
  --blue:#1d8fd0;
  --orange:#ff4a12;
  --label-blue:#1a73d1;
  --text:#333;
  --muted:#777;
  --line:#bdbdbd;
  --slot:#d6d6d6;
  --footer:#e4e4e4;
}
*{box-sizing:border-box;margin:0;padding:0}
html,body{width:1151px;height:1200px;overflow:hidden;background:var(--white);font-family:'Lato',sans-serif;color:var(--text)}
.canvas{position:relative;width:1151px;height:1200px}
.site-header{position:absolute;left:0;top:0;width:100%;height:112px;background:var(--ink)}
.brand{position:absolute;left:162px;top:30px;display:flex;align-items:center;gap:12px}
.brand-square{width:40px;height:40px;background:var(--white)}
.brand-name{color:var(--white);font-weight:700;font-size:17px;line-height:21px;width:160px}
.main-nav{position:absolute;left:526px;top:40px;height:39px;display:flex;border:1px solid #ddd}
.main-nav a{color:var(--white);text-decoration:none;font-size:14px;display:flex;align-items:center;justify-content:center;border-right:1px solid #ddd}
.main-nav a:last-child{border-right:none}
.report{position:absolute;left:162px;top:164px;width:620px;height:900px;background:var(--white);box-shadow:0 1px 5px rgba(0,0,0,.3)}
.compass{position:absolute;left:160px;top:26px;width:292px;height:292px;border-radius:50%;background:radial-gradient(circle,#fff 30%,#d9e3ee 55%,#0d2f5a 57%,#eaf0f6 60%,#fff 90%,#0d2f5a 92%)}
.metric-title{position:absolute;font-size:18px;color:#222;letter-spacing:.2px}
.battery{position:absolute;width:202px;height:45px;border:2px solid var(--line);padding:4px}
.battery::after{content:"";position:absolute;right:-9px;top:10px;width:7px;height:21px;border:2px solid var(--line);border-left:none}
.battery-fill{display:flex;height:100%}
.battery-fill span{flex:1}
.fill-blue{background:var(--blue)}
.fill-orange{background:var(--orange)}
.icon{position:absolute}
.column{position:absolute;width:70px;height:125px;background:var(--slot);padding:5px;display:flex;flex-direction:column}
.column span{display:block}
.scale{position:absolute;left:276px;top:476px;list-style:none;font-size:14px;color:#666;width:40px;text-align:center}
.scale li{height:26px}
.field-label{position:absolute;width:117px;text-align:right;color:var(--label-blue);font-size:15px}
.field{position:absolute;left:136px;width:424px;border:1px solid var(--line);background:linear-gradient(#fafafa,#e6e6e6);font-size:14px;color:#444;padding:0 16px;display:flex;align-items:center}
.field-profile{align-items:flex-start;padding:16px 20px;font-size:11px;line-height:18px;color:var(--muted)}
.site-footer{position:absolute;left:0;top:1130px;width:100%;height:70px;background:var(--footer);border-top:1px solid #c8c8c8}
.site-footer p{position:absolute;left:750px;top:25px;font-size:12px;color:#444}
</style>
</head>
<body>
<div class="canvas">
  <header class="site-header">
    <div class="brand">
      <span class="brand-square"></span>
      <span class="brand-name">Ravnaas-Lilleby Group</span>
    </div>
    <nav class="main-nav">
      <a href="#" style="width:89px">Home</a>
      <a href="#" style="width:96px">About Us</a>
      <a href="#" style="width:86px">Product</a>
      <a href="#" style="width:68px">Jobs</a>
      <a href="#" style="width:121px">Contact Us</a>
    </nav>
  </header>

  <main class="report">
    <div class="compass" role="img" aria-label="Nautical compass rose illustration in navy blue"></div>

    <h2 class="metric-title" style="left:75px;top:338px">ENERGY</h2>
    <div class="battery" style="left:74px;top:367px"><div class="battery-fill"><span class="fill-blue"></span><span class="fill-orange"></span></div></div>

    <h2 class="metric-title" style="left:367px;top:338px">PROBLEM SOLVE</h2>
    <div class="battery" style="left:367px;top:365px"><div class="battery-fill"><span class="fill-blue"></span><span class="fill-orange"></span></div></div>

    <h2 class="metric-title" style="left:75px;top:434px">LISTEN</h2>
    <svg class="icon" style="left:135px;top:423px" width="40" height="40" viewBox="0 0 40 40" aria-hidden="true">
      <g fill="none" stroke="#1d8fd0" stroke-width="2.5"><circle cx="20" cy="20" r="18"/><circle cx="20" cy="20" r="12"/><circle cx="20" cy="20" r="6"/></g>
      <circle cx="20" cy="20" r="2" fill="#1d8fd0"/>
    </svg>

    <h2 class="metric-title" style="left:368px;top:434px">SENDING</h2>
    <svg class="icon" style="left:455px;top:428px" width="42" height="32" viewBox="0 0 42 32" aria-hidden="true">
      <g fill="none" stroke="#ff4a12" stroke-width="3" stroke-linejoin="round"><path d="M3 10h9l25-8v26l-25-6H3z"/><path d="M12 10v12"/><path d="M8 22l3 8h5l-2-8"/></g>
    </svg>

    <div class="column" style="left:76px;top:470px"><span class="fill-orange" style="height:30%"></span><span class="fill-blue" style="flex:1"></span></div>
    <div class="column" style="left:153px;top:470px"><span class="fill-orange" style="height:77%"></span><span class="fill-blue" style="flex:1"></span></div>

    <ol class="scale"><li>- 1 -</li><li>- 2 -</li><li>- 3 -</li><li>- 4 -</li><li>- 5 -</li></ol>

    <div class="column" style="left:370px;top:470px"><span class="fill-orange" style="height:50%"></span><span class="fill-blue" style="flex:1"></span></div>
    <div class="column" style="left:448px;top:470px"><span class="fill-orange" style="height:77%"></span><span class="fill-blue" style="flex:1"></span></div>

    <span class="field-label" style="left:0;top:646px">Name:</span>
    <div class="field" style="top:641px;height:38px">Erik Solberg</div>

    <span class="field-label" style="left:0;top:698px">Company:</span>
    <div class="field" style="top:693px;height:38px">Norvik Partners Limited</div>

    <span class="field-label" style="left:0;top:746px">Profile:</span>
    <div class="field field-profile" style="top:742px;height:108px">Morbi diam mauris viverra in gravida eu mattis in ante Morbi eget arcu Morbi porta libero id ullamcorper nonummy nibh ligula pulvinar metus eget consectetuer augue nisi quis lacus Ut ac mi quis lacus mollis aliquam Curabitur iaculis tempus eros Curabitur vel mi sit amet magna malesuad</div>
  </main>

  <footer class="site-footer">
    <p>© 2017 Company Name&nbsp; All right reserved&nbsp; Terms of Use</p>
  </footer>
</div>
</body>
</html>
```